Scrum Master & Agile IT Coach Needing Business Website

Hello, my name is Joel Brandt
I am a project manger, scrum master, & agile coach. I work with IT development teams on major projects for Summit 300 companies . My project management business has a website and can be found here: www.tk-steadfast.example

I have launched a new company, ALL focused on IT Agile Coaching, I am looking to have a website created for my new company - the name of the new company is: Q's and V's - Agile IT Coaching and Training.
I have a logo and it is provided in the materials. I like to logo; I am open to different color pallets.

The website will have a total of 7 pages; I have content for 5 of the 7 pages prepared; the other 2 pages will say under construction.

Page 1 Who am I, What I do, My Experience
Demonstrated experience and progression from Scrum Master to
Program Manager to Coach

Page 2 Q's & V's - Agile Team Coaching
teams working major IT projects, multiple months/years

Page 3 Coaching @ the Team Level

Page 4 Coaching @ the Program Level ; LIMBr ART level

Pages 5 -6 Under Construction

Page 7 Presentations, Slide Decks, Reference Materials

Mentors Nook need to have this highlighted somewhere Monthly Blog
Updates

Industry/Entity Type

IT development

Coding

Coded - Design and coding required

Number of Pages Required

5+ page

Requirements
Must have
• the website must be bold - I want those who visit to remember coming to my coaching site
Nice to have
• nice to have will be a modern / futuristic website; I work with IT developers, I want a website they will like
Should not have
• should not be stiff - it should be professional but fun

```html
<!DOCTYPE html>
<html lang="en">
<head>
<meta charset="utf-8">
<title>Brandt Agile - Coaching @ the Team Level</title>
<link rel="stylesheet" href="https://fonts.googleapis.com/css2?family=Oswald:wght@500;600&family=Poppins:ital,wght@0,400;0,500;0,600;1,400&display=swap">
<style>
:root{
  --teal:#1db59b;
  --teal-soft:#e3f6f1;
  --ink:#1d1d1d;
  --text:#555a5e;
  --muted:#8a8f93;
  --grey-band:#f1f2f3;
  --card:#ffffff;
  --footer:#1c1c1e;
  --hero-a:#2f3f46;
  --hero-b:#6f8a8e;
}
*{box-sizing:border-box;margin:0;padding:0}
html,body{width:1200px;height:3144px;overflow:hidden;background:#fff}
body{font-family:'Poppins',sans-serif;color:var(--text);position:relative}
.heading{font-family:'Oswald',sans-serif;font-weight:600;color:var(--ink);text-transform:uppercase;letter-spacing:.5px}
.eyebrow{font-size:17px;font-weight:600;color:var(--teal);text-transform:uppercase;letter-spacing:.5px}

/* header */
.site-header{position:absolute;top:0;left:0;width:1200px;height:80px;display:flex;align-items:center;justify-content:space-between;padding:0 60px 0 70px;background:#fff}
.brand{display:flex;align-items:center;gap:12px;font-family:'Poppins',sans-serif;font-weight:600;font-size:24px;color:var(--ink)}
.brand-mark{width:26px;height:26px;background:var(--teal)}
.main-nav{display:flex;gap:34px}
.main-nav a{font-size:15px;color:var(--ink);text-decoration:none;line-height:1.2;max-width:120px}
.main-nav a.active{color:var(--teal)}

/* hero */
.hero{position:absolute;top:80px;left:0;width:1200px;height:520px;background:linear-gradient(120deg,var(--hero-a),var(--hero-b) 60%,#b9c8c6);clip-path:polygon(0 0,100% 0,100% 84%,0 100%)}
.hero-copy{position:absolute;left:112px;top:170px}
.hero-kicker{font-size:18px;color:var(--teal);font-weight:500;margin-bottom:6px}
.hero-title{font-family:'Oswald',sans-serif;font-weight:600;font-size:56px;line-height:1.1;color:#fff;text-transform:uppercase}

/* values */
.values{position:absolute;top:600px;left:0;width:1200px;height:470px}
.values-intro{position:absolute;left:112px;top:40px;width:380px}
.values-intro .heading{font-size:44px;margin:8px 0 18px}
.values-intro p{font-size:16px;line-height:1.6;color:var(--muted)}
.btn{display:inline-block;margin-top:30px;background:var(--teal);color:#fff;font-size:15px;font-weight:600;padding:16px 26px;text-transform:uppercase;text-decoration:none}
.value-grid{position:absolute;left:540px;top:-60px;width:560px;display:grid;grid-template-columns:1fr 1fr;row-gap:34px}
.value{text-align:center}
.value-icon{width:130px;height:130px;border-radius:50%;background:var(--teal-soft);margin:0 auto 14px;display:flex;align-items:center;justify-content:center}
.value h3{font-size:17px;font-weight:500;color:var(--ink)}
.value p{font-size:15px;color:var(--muted)}

/* principles */
.principles{position:absolute;top:1070px;left:0;width:1200px;height:860px;background:var(--grey-band);clip-path:polygon(0 4%,100% 0,100% 100%,0 100%)}
.principles-head{text-align:center;padding-top:100px}
.principles-head .heading{font-size:44px;margin-top:8px}
.principle-grid{position:absolute;left:112px;top:220px;width:976px;display:grid;grid-template-columns:repeat(4,1fr);gap:20px}
.principle{background:var(--card);height:180px;padding:18px 20px;display:flex;align-items:center;justify-content:center;text-align:center;font-style:italic;font-size:14px;line-height:1.5;color:var(--text);box-shadow:0 4px 16px rgba(0,0,0,.06)}

/* team level */
.team{position:absolute;top:1960px;left:0;width:1200px;height:660px}
.team-head{text-align:center;padding-top:40px}
.team-head .heading{font-size:50px;margin-top:8px}
.team-photo{position:absolute;left:112px;top:180px;width:450px;height:420px;background:linear-gradient(135deg,#c7a58d,#8b6a57 50%,#3d4a52)}
.team-list{position:absolute;left:584px;top:196px;width:504px;height:390px;background:#fff;box-shadow:0 6px 28px rgba(0,0,0,.1);padding:30px 34px;list-style:none}
.team-list li{display:flex;align-items:flex-start;gap:14px;font-size:16px;color:var(--ink);margin-bottom:12px;line-height:1.35}
.team-list svg{flex:none;margin-top:2px}

/* footer */
.site-footer{position:absolute;top:2620px;left:0;width:1200px;height:524px;background:var(--footer);clip-path:polygon(0 22%,100% 0,100% 100%,0 100%);color:#fff}
.footer-brand{position:absolute;left:112px;top:218px;display:flex;align-items:center;gap:12px;font-weight:600;font-size:30px}
.footer-col{position:absolute;top:140px}
.footer-col h4{font-size:16px;font-weight:600;margin-bottom:14px}
.footer-col a,.footer-col span{display:flex;align-items:center;gap:8px;font-size:14px;color:#e6e6e6;text-decoration:none;margin-bottom:10px;line-height:1.3}
.quick{left:540px;width:230px}
.contact{left:848px;width:280px}
.footer-bottom{position:absolute;left:112px;right:80px;top:460px;display:flex;justify-content:space-between;align-items:center;font-size:14px;color:#ddd}
.social{display:flex;gap:14px}
.social i{display:block;width:30px;height:30px;border-radius:50%;border:2px solid var(--teal)}
</style>
</head>
<body>

<header class="site-header">
  <div class="brand"><span class="brand-mark"></span>Brandt Agile</div>
  <nav class="main-nav">
    <a href="#">Agile Coaching</a>
    <a href="#" class="active">Coaching @ the Team Level</a>
    <a href="#">Coaching @ the Program Level</a>
    <a href="#">Mentors Nook</a>
    <a href="#">Reference Materials</a>
  </nav>
</header>

<section class="hero" role="img" aria-label="Photo of a development team collaborating around a laptop">
  <div class="hero-copy">
    <p class="hero-kicker">Q's and V's</p>
    <h1 class="hero-title">Coaching<br>@ The Team Level</h1>
  </div>
</section>

<section class="values">
  <div class="values-intro">
    <p class="eyebrow">Agile Software Development</p>
    <h2 class="heading">Scrum Values</h2>
    <p>We are uncovering better ways of developing software by doing it and helping others do it. Through this work we have come to value:</p>
    <a class="btn" href="#">Read More</a>
  </div>
  <div class="value-grid">
    <div class="value">
      <div class="value-icon"><svg width="60" height="60" viewBox="0 0 60 60" fill="none" stroke="#1db59b" stroke-width="2.5"><circle cx="20" cy="18" r="7"/><circle cx="40" cy="18" r="7"/><path d="M8 44c0-8 5-13 12-13s12 5 12 13M28 44c0-8 5-13 12-13s12 5 12 13"/></svg></div>
      <h3>Individuals and interactions</h3><p>over process and tools</p>
    </div>
    <div class="value">
      <div class="value-icon"><svg width="60" height="60" viewBox="0 0 60 60" fill="none" stroke="#1db59b" stroke-width="2.5"><rect x="8" y="12" width="44" height="30" rx="2"/><path d="M22 50h16M30 42v8M20 27l6 6 14-14"/></svg></div>
      <h3>Working software</h3><p>over comprehensive documentation</p>
    </div>
    <div class="value">
      <div class="value-icon"><svg width="60" height="60" viewBox="0 0 60 60" fill="none" stroke="#1db59b" stroke-width="2.5"><path d="M6 26l10-8 10 6 8-4 8 4 12-4M16 30l10 10 6-4 8 6 10-10M26 40l-6 6"/></svg></div>
      <h3>Customer collaboration</h3><p>over contract negotiation</p>
    </div>
    <div class="value">
      <div class="value-icon"><svg width="60" height="60" viewBox="0 0 60 60" fill="none" stroke="#1db59b" stroke-width="2.5"><rect x="8" y="10" width="30" height="20" rx="3"/><path d="M14 30v7l7-7"/><rect x="24" y="28" width="28" height="18" rx="3"/><path d="M44 46v7l-7-7M30 37h16"/></svg></div>
      <h3>Responding to change</h3><p>over following a plan</p>
    </div>
  </div>
</section>

<section class="principles">
  <div class="principles-head">
    <p class="eyebrow">Our Principles</p>
    <h2 class="heading">We Follow These Principles</h2>
  </div>
  <div class="principle-grid">
    <div class="principle">Our highest priority is to satisfy the customer through early and continuous delivery of valuable software.</div>
    <div class="principle">Welcome changing requirements, even late in development. Agile processes harness change for the customer's competitive advantage.</div>
    <div class="principle">Deliver working software frequently, from a couple of weeks to a couple of months, with a preference to the shorter timescale.</div>
    <div class="principle">Business people and developers must work together daily throughout the project.</div>
    <div class="principle">Build projects around motivated individuals. Give them the environment and support they need, and trust them to get the job done.</div>
    <div class="principle">The most efficient and effective method of conveying information to and within a development team is face-to-face conversation.</div>
    <div class="principle">Working software is the primary measure of progress.</div>
    <div class="principle">Agile processes promote sustainable development. The sponsors, developers, and users should be able to maintain a constant pace indefinitely.</div>
    <div class="principle">Continuous attention to technical excellence and good design enhances agility.</div>
    <div class="principle">Simplicity—the art of maximizing the amount of work not done—is essential.</div>
    <div class="principle">Simplicity—the art of maximizing the amount of work not done—is essential.</div>
    <div class="principle">At regular intervals, the team reflects on how to become more effective, then tunes and adjusts its behavior accordingly.</div>
  </div>
</section>

<section class="team">
  <div class="team-head">
    <p class="eyebrow">Coaching &amp; Running Teams</p>
    <h2 class="heading">@ The Team Level</h2>
  </div>
  <div class="team-photo" role="img" aria-label="Photo of team members stacking hands together"></div>
  <ul class="team-list">
    <li><svg width="18" height="18" viewBox="0 0 18 18"><circle cx="9" cy="9" r="9" fill="#1db59b"/><path d="M5 9.5l2.7 2.7L13 6.5" stroke="#fff" stroke-width="2" fill="none"/></svg>Team Working Agreements</li>
    <li><svg width="18" height="18" viewBox="0 0 18 18"><circle cx="9" cy="9" r="9" fill="#1db59b"/><path d="M5 9.5l2.7 2.7L13 6.5" stroke="#fff" stroke-width="2" fill="none"/></svg>Stakeholder Communications Plans</li>
    <li><svg width="18" height="18" viewBox="0 0 18 18"><circle cx="9" cy="9" r="9" fill="#1db59b"/><path d="M5 9.5l2.7 2.7L13 6.5" stroke="#fff" stroke-width="2" fill="none"/></svg>Team Words: Honesty, Respect, Transparency, Dependability</li>
    <li><svg width="18" height="18" viewBox="0 0 18 18"><circle cx="9" cy="9" r="9" fill="#1db59b"/><path d="M5 9.5l2.7 2.7L13 6.5" stroke="#fff" stroke-width="2" fill="none"/></svg>Forming Storming, Norming Performing</li>
    <li><svg width="18" height="18" viewBox="0 0 18 18"><circle cx="9" cy="9" r="9" fill="#1db59b"/><path d="M5 9.5l2.7 2.7L13 6.5" stroke="#fff" stroke-width="2" fill="none"/></svg>Re tooling and Sharpening</li>
    <li><svg width="18" height="18" viewBox="0 0 18 18"><circle cx="9" cy="9" r="9" fill="#1db59b"/><path d="M5 9.5l2.7 2.7L13 6.5" stroke="#fff" stroke-width="2" fill="none"/></svg>Team Member Assessments</li>
    <li><svg width="18" height="18" viewBox="0 0 18 18"><circle cx="9" cy="9" r="9" fill="#1db59b"/><path d="M5 9.5l2.7 2.7L13 6.5" stroke="#fff" stroke-width="2" fill="none"/></svg>Agile Team Assessments</li>
    <li><svg width="18" height="18" viewBox="0 0 18 18"><circle cx="9" cy="9" r="9" fill="#1db59b"/><path d="M5 9.5l2.7 2.7L13 6.5" stroke="#fff" stroke-width="2" fill="none"/></svg>Team Retrospectives</li>
    <li><svg width="18" height="18" viewBox="0 0 18 18"><circle cx="9" cy="9" r="9" fill="#1db59b"/><path d="M5 9.5l2.7 2.7L13 6.5" stroke="#fff" stroke-width="2" fill="none"/></svg>Project / Program Lessons Learned</li>
  </ul>
</section>

<footer class="site-footer">
  <div class="footer-brand"><span class="brand-mark"></span>Brandt Agile</div>
  <div class="footer-col quick">
    <h4>Quick Links</h4>
    <a href="#">Home</a>
    <a href="#">Agile Team Coaching</a>
    <a href="#">Coaching @ the Team Level</a>
    <a href="#">Coaching @ the Program Level ; LIMBr ART Level</a>
    <a href="#">Mentors Nook</a>
    <a href="#">Contact</a>
  </div>
  <div class="footer-col contact">
    <h4>Contact Us</h4>
    <span><svg width="14" height="14" viewBox="0 0 14 14"><path d="M3 1l2 3-1.3 1.3a8 8 0 0 0 5 5L10 9l3 2-1 2.5C6 13 1 8 .5 2z" fill="#1db59b"/></svg>1 555 010 4422</span>
    <span><svg width="14" height="14" viewBox="0 0 14 14"><rect x="1" y="3" width="12" height="8" fill="none" stroke="#1db59b" stroke-width="1.5"/><path d="M1 3l6 5 6-5" fill="none" stroke="#1db59b" stroke-width="1.5"/></svg>joel.brandt@qv-coaching.example</span>
    <span><svg width="14" height="14" viewBox="0 0 14 14"><path d="M7 13S2 8 2 5a5 5 0 0 1 10 0c0 3-5 8-5 8z" fill="#1db59b"/><circle cx="7" cy="5" r="1.8" fill="#1c1c1e"/></svg>Remote Location</span>
  </div>
  <div class="footer-bottom">
    <span>Copyright © 2022 Q's and V's - Agile IT Coaching and Training - all rights reserved.</span>
    <div class="social"><i></i><i></i><i></i></div>
  </div>
</footer>

</body>
</html>
```